Awesome photographers card for an awesome new business

Double sided business card Black background and silver logo in middle on one side. Details on otherside. please keep it simple

Industry/Entity Type

Photographer

Contact Information for Business Card

Gerald Fenwick
0452817360
GeraldFenwickPhotography47@mailbox.test
www.GeraldFenwickPhotography.test.au
Instagram _Gerald_fenwick

Requirements
Must have
• My logo in Silver
• please use instagram logo instead of "Instagram"

```html
<!DOCTYPE html>
<html lang="en">
<head>
<meta charset="utf-8">
<title>Gerald Fenwick Photography – Business Card</title>
<link rel="stylesheet" href="https://fonts.googleapis.com/css2?family=Roboto:wght@400;500&family=Roboto+Condensed:wght@700&display=swap">
<style>
  :root {
    --stage: #262626;
    --card-black: #1b1c1d;
    --silver-light: #e9e9e9;
    --silver-mid: #c4c4c4;
    --silver-dark: #9a9a9a;
    --shadow-band: #6d6d6d;
    --ink: #1a1a1a;
    --logo-silver: #d2d2d2;
    --url-grey: #d8d8d8;
  }
  * { margin: 0; padding: 0; box-sizing: border-box; }
  html, body { width: 1200px; height: 960px; overflow: hidden; }
  body { background: var(--stage); font-family: "Roboto", sans-serif; position: relative; }

  .card {
    position: absolute;
    width: 600px;
    height: 342px;
    background: var(--card-black);
    overflow: hidden;
    box-shadow: 0 2px 8px rgba(0,0,0,0.45);
  }
  .card--front { left: 314px; top: 113px; }
  .card--back  { left: 312px; top: 473px; }

  .wave { position: absolute; inset: 0; width: 600px; height: 342px; }

  .logo-mark {
    position: absolute;
    border: 2px solid var(--logo-silver);
    border-radius: 50%;
    display: flex;
    align-items: center;
    justify-content: center;
    text-align: center;
  }
  .logo-mark__name {
    font-family: "Roboto", sans-serif;
    font-weight: 500;
    color: var(--logo-silver);
    font-size: 19px;
    letter-spacing: 2px;
    line-height: 1.3;
    text-transform: uppercase;
  }
  .card--front .logo-mark { left: 59px; top: 20px; width: 164px; height: 164px; }
  .card--back .logo-mark  { left: 216px; top: 80px; width: 164px; height: 164px; }

  .contact {
    position: absolute;
    right: 21px;
    top: 204px;
    text-align: right;
    color: var(--ink);
  }
  .contact__name {
    font-family: "Roboto Condensed", sans-serif;
    font-weight: 700;
    font-size: 20px;
    letter-spacing: 0.3px;
    text-transform: uppercase;
    margin-bottom: 14px;
  }
  .contact__list { list-style: none; }
  .contact__item {
    display: flex;
    justify-content: flex-end;
    align-items: center;
    gap: 8px;
    font-size: 14px;
    line-height: 19px;
  }
  .contact__icon { width: 13px; height: 13px; flex: none; }
  .contact__icon--square { width: 12px; height: 12px; background: var(--ink); }

  .site-url {
    position: absolute;
    left: 0; right: 0;
    top: 290px;
    text-align: center;
    color: var(--url-grey);
    font-size: 14px;
    letter-spacing: 2px;
  }
</style>
</head>
<body>

<section class="card card--front" aria-label="Business card, contact side">
  <svg class="wave" viewBox="0 0 600 342" aria-hidden="true">
    <defs>
      <linearGradient id="silverFill" x1="0" y1="0" x2="1" y2="1">
        <stop offset="0" stop-color="#cfcfcf"/>
        <stop offset="0.45" stop-color="#ececec"/>
        <stop offset="1" stop-color="#b9b9b9"/>
      </linearGradient>
    </defs>
    <path d="M0 242 C80 250 150 296 240 250 C320 205 380 120 450 86 C510 60 570 66 600 70 L600 342 L0 342 Z" fill="var(--shadow-band)"/>
    <path d="M0 250 C80 260 160 302 250 262 C330 222 390 140 460 100 C520 72 570 80 600 84 L600 342 L0 342 Z" fill="var(--ink)"/>
    <path d="M0 254 C80 266 160 306 252 266 C334 226 394 146 464 106 C522 80 570 86 600 90 L600 342 L0 342 Z" fill="url(#silverFill)"/>
  </svg>

  <div class="logo-mark">
    <span class="logo-mark__name">Gerald<br>Fenwick</span>
  </div>

  <div class="contact">
    <h1 class="contact__name">Gerald Fenwick</h1>
    <ul class="contact__list">
      <li class="contact__item">0452817360
        <svg class="contact__icon" viewBox="0 0 16 16" aria-hidden="true"><path d="M3.5 1.5l3 3-1.8 1.8c.8 1.8 2.2 3.2 4 4l1.8-1.8 3 3-1.8 2.2C6.5 13.7 2.3 9.5 1.5 3.3z" fill="var(--ink)"/></svg>
      </li>
      <li class="contact__item">GeraldFenwickPhotography47@mailbox.test
        <svg class="contact__icon" viewBox="0 0 16 16" aria-hidden="true"><rect x="1" y="3" width="14" height="10" fill="var(--ink)"/><path d="M1.5 3.5L8 8.5l6.5-5" fill="none" stroke="#ddd" stroke-width="1.2"/></svg>
      </li>
      <li class="contact__item">www.GeraldFenwickPhotography.test.au
        <svg class="contact__icon" viewBox="0 0 16 16" aria-hidden="true"><circle cx="8" cy="8" r="6.5" fill="var(--ink)"/><path d="M1.5 8h13M8 1.5c-3 3.5-3 9.5 0 13M8 1.5c3 3.5 3 9.5 0 13" fill="none" stroke="#ddd" stroke-width="1"/></svg>
      </li>
      <li class="contact__item">Gerald_fenwick
        <span class="contact__icon contact__icon--square" aria-hidden="true"></span>
      </li>
    </ul>
  </div>
</section>

<section class="card card--back" aria-label="Business card, logo side">
  <div class="logo-mark">
    <span class="logo-mark__name">Gerald<br>Fenwick</span>
  </div>
  <p class="site-url">www.GeraldFenwickPhotography.test.au</p>
</section>

</body>
</html>
```